BOLD & MINIMALIST DESIGN NEEDED

We want a very bold but minimalistic business card design that is impactful and utilizes both sides of the business card. Our current logo is included for your use.

We want bold fonts and good use of negative space. We don't want the logo to overpower the design.

Target Market(s)

Professionals who are building new commercial buildings.

Industry/Entity Type

Construction

Contact Information for Business Card

Name, Title, email, office phone, cell phone, website

Font styles to use
Serif
Sans Serif

Requirements
Must have
• Bold design!

```html
<!DOCTYPE html>
<html lang="en">
<head>
<meta charset="utf-8">
<title>Ridgeline Design + Build — Business Card</title>
<link href="https://fonts.googleapis.com/css2?family=Lato:wght@400;700&family=Montserrat:wght@800&display=swap" rel="stylesheet">
<style>
  :root {
    --canvas: #ecebe8;
    --green-dark: #2f560d;
    --green-mid: #4f8a1e;
    --green-bright: #86c232;
    --ink: #111111;
    --text-grey: #666666;
    --paper: #ffffff;
  }
  * { margin: 0; padding: 0; box-sizing: border-box; }
  html, body { width: 1200px; height: 800px; overflow: hidden; }
  body {
    background: var(--canvas);
    font-family: "Lato", sans-serif;
    display: flex;
    align-items: center;
    justify-content: center;
    gap: 40px;
  }
  .card {
    width: 540px;
    height: 309px;
    position: relative;
    overflow: hidden;
    box-shadow: 0 10px 26px rgba(0,0,0,0.22);
  }

  /* Front */
  .card-front {
    background: radial-gradient(ellipse at 55% 40%, var(--green-mid) 0%, var(--green-dark) 100%);
    display: flex;
    align-items: center;
    justify-content: center;
  }
  .brand-name {
    font-family: "Montserrat", sans-serif;
    font-weight: 800;
    text-transform: uppercase;
    letter-spacing: 1px;
    text-align: center;
    line-height: 1.05;
  }
  .card-front .brand-name { color: var(--paper); font-size: 44px; }
  .card-front .brand-name span { display: block; font-size: 18px; letter-spacing: 6px; margin-top: 6px; }

  /* Back */
  .card-back { background: var(--paper); }
  .card-back .brand-name {
    position: absolute; top: 34px; right: 32px;
    color: var(--ink); font-size: 26px; text-align: right;
  }
  .card-back .brand-name span { display: block; font-size: 11px; letter-spacing: 3.5px; margin-top: 4px; }

  .contact-block { position: absolute; left: 34px; top: 100px; z-index: 1; }
  .person-name {
    font-family: "Montserrat", sans-serif; font-weight: 800;
    font-size: 21px; text-transform: uppercase; color: var(--ink);
  }
  .person-name .surname { color: var(--green-bright); }
  .person-title { font-size: 15px; color: var(--text-grey); margin-top: 2px; }
  .person-title .role { color: var(--green-bright); }
  .address { font-size: 14px; color: var(--text-grey); line-height: 1.3; margin-top: 4px; }

  .contact-list { list-style: none; margin-top: 20px; }
  .contact-list li {
    display: flex; align-items: center; gap: 8px;
    font-size: 15px; color: var(--ink); line-height: 1.45;
  }
  .icon-box {
    width: 17px; height: 17px; border-radius: 3px;
    background: var(--green-bright);
    display: inline-flex; align-items: center; justify-content: center;
  }

  .swoosh { position: absolute; left: 0; bottom: 0; width: 540px; height: 309px; }
  .web-address {
    position: absolute; right: 24px; bottom: 112px;
    transform: rotate(-18deg); transform-origin: right center;
    color: var(--paper); font-size: 14px;
    display: flex; align-items: center; gap: 6px;
  }
</style>
</head>
<body>

  <section class="card card-front">
    <div class="brand-name">Ridgeline<span>Design + Build</span></div>
  </section>

  <section class="card card-back">
    <div class="brand-name">Ridgeline<span>Design + Build</span></div>

    <svg class="swoosh" viewBox="0 0 540 309" aria-hidden="true">
      <path d="M0,309 L0,303 C150,308 250,283 320,223 C390,163 460,129 540,133 L540,309 Z" fill="var(--green-bright)"/>
      <path d="M0,294 C150,299 245,272 314,212 C384,152 456,116 540,120 L540,126 C458,122 388,158 318,218 C248,278 150,304 0,299 Z" fill="var(--ink)"/>
    </svg>

    <div class="contact-block">
      <p class="person-name">Marcus <span class="surname">Hale</span></p>
      <p class="person-title"><span class="role">Founder</span> &amp; CEO</p>
      <p class="address">4417 Harbor Stone Blvd 210-C,<br>FL 32561</p>

      <ul class="contact-list">
        <li>
          <span class="icon-box">
            <svg width="11" height="11" viewBox="0 0 24 24"><path fill="#fff" d="M6.6 10.8a15 15 0 0 0 6.6 6.6l2.2-2.2c.3-.3.7-.4 1-.2 1.1.4 2.3.6 3.6.6.6 0 1 .4 1 1V20c0 .6-.4 1-1 1A17 17 0 0 1 3 4c0-.6.4-1 1-1h3.5c.6 0 1 .4 1 1 0 1.3.2 2.5.6 3.6.1.3 0 .7-.2 1z"/></svg>
          </span>021-555-304-816
        </li>
        <li>
          <span class="icon-box">
            <svg width="11" height="11" viewBox="0 0 24 24"><rect x="6" y="2" width="12" height="20" rx="2" fill="#fff"/><rect x="8" y="5" width="8" height="12" fill="var(--green-bright)"/></svg>
          </span>047-555-219-630
        </li>
        <li>
          <span class="icon-box">
            <svg width="11" height="11" viewBox="0 0 24 24"><path fill="#fff" d="M2 21 23 12 2 3v7l15 2-15 2z"/></svg>
          </span>hello@ridgelinebuild.com
        </li>
      </ul>
    </div>

    <div class="web-address">
      <svg width="16" height="16" viewBox="0 0 24 24"><rect x="1" y="1" width="22" height="22" rx="4" fill="#fff"/><circle cx="12" cy="12" r="7" fill="none" stroke="var(--green-bright)" stroke-width="2"/><path d="M5 12h14M12 5v14" stroke="var(--green-bright)" stroke-width="2"/></svg>
      www.ridgelinebuild.com
    </div>
  </section>

</body>
</html>
```